Business Card Design Project

I am opening a skin care studio called Glow Haven by Marisol. I will be offering a wide range of unique and affordable skin services including facials, chemical peels, microdermabrasion treatments, body wraps, salt glows, all waxing and eye lash extensions. If the business cards depicts what I would like, this would lead to brochures, web design, signs, etc.

Project Deadline Extended
Reason: A request to extend deadline was requested. I will be more than happy to accommodate.

Industry/Entity Type

Business

Requirements
Nice to have
• facial features so prospective client clearly identifies what type of business this is. Not stuffy or boring "spa" looking graphics. I am focusing just on face, body, waxing, eyelashes. No massage or nails.

```html
<!DOCTYPE html>
<html lang="en">
<head>
<meta charset="utf-8">
<title>Glow Haven by Marisol — Business Cards</title>
<link rel="stylesheet" href="https://fonts.googleapis.com/css2?family=Questrial&family=Oswald:wght@400&family=Arimo:wght@400&display=swap">
<style>
  :root {
    --canvas-bg: #ececec;
    --card-black: #141414;
    --card-paper: #f7f6f3;
    --ink-white: #ffffff;
    --ink-black: #111111;
    --art-teal: #1e9aa0;
    --art-violet: #6a5a9e;
    --art-rose: #e98fb0;
    --art-peach: #f4c2a6;
    --art-blush: #f6dbe4;
  }
  * { box-sizing: border-box; margin: 0; padding: 0; }
  html, body {
    width: 1200px;
    height: 1200px;
    overflow: hidden;
    background: var(--canvas-bg);
  }
  .sheet {
    width: 1200px;
    height: 1200px;
    display: flex;
    flex-direction: column;
    align-items: center;
    justify-content: center;
    gap: 52px;
  }
  .card {
    width: 900px;
    height: 514px;
    position: relative;
    overflow: hidden;
    box-shadow: 0 6px 22px rgba(0,0,0,0.18);
  }

  /* Front */
  .card--front {
    background: var(--card-black);
    color: var(--ink-white);
    display: flex;
    flex-direction: column;
    align-items: center;
    justify-content: center;
    font-family: "Questrial", "Century Gothic", sans-serif;
  }
  .brand-name {
    font-size: 86px;
    font-weight: 400;
    letter-spacing: 3px;
    line-height: 1;
  }
  .brand-owner {
    font-size: 36px;
    margin-top: 14px;
    letter-spacing: 1px;
  }

  /* Back */
  .card--back {
    background: var(--card-paper);
    color: var(--ink-black);
  }
  .portrait-art {
    position: absolute;
    left: 0;
    top: 0;
    width: 340px;
    height: 100%;
  }
  .appointment {
    position: absolute;
    left: 410px;
    top: 62px;
    font-family: "Oswald", "Arial Narrow", sans-serif;
    font-size: 44px;
    line-height: 1.35;
    letter-spacing: 0.5px;
  }
  .appointment__title { margin-bottom: 14px; }
  .contact {
    position: absolute;
    right: 44px;
    bottom: 40px;
    text-align: right;
    font-family: "Arimo", Arial, sans-serif;
    font-size: 32px;
    line-height: 1.3;
    list-style: none;
  }
</style>
</head>
<body>
<main class="sheet">
  <section class="card card--front">
    <h1 class="brand-name">GLOW HAVEN</h1>
    <p class="brand-owner">by marisol</p>
  </section>

  <section class="card card--back">
    <svg class="portrait-art" viewBox="0 0 340 514" role="img" aria-label="Colourful painted close-up illustration of an eye with teal iris in pink, violet and peach tones">
      <defs>
        <linearGradient id="artTones" x1="0" y1="0" x2="0.3" y2="1">
          <stop offset="0" stop-color="var(--art-violet)"/>
          <stop offset="0.4" stop-color="var(--art-teal)"/>
          <stop offset="0.7" stop-color="var(--art-rose)"/>
          <stop offset="1" stop-color="var(--art-peach)"/>
        </linearGradient>
        <linearGradient id="artFade" x1="0" y1="0" x2="1" y2="0">
          <stop offset="0.6" stop-color="var(--card-paper)" stop-opacity="0"/>
          <stop offset="1" stop-color="var(--card-paper)" stop-opacity="0.85"/>
        </linearGradient>
      </defs>
      <path d="M0 0 H220 C300 80 330 200 300 320 C280 420 230 480 200 514 H0 Z" fill="url(#artTones)"/>
      <path d="M0 0 H220 C300 80 330 200 300 320 C280 420 230 480 200 514 H0 Z" fill="url(#artFade)"/>
    </svg>

    <div class="appointment">
      <p class="appointment__title">APPOINTMENT</p>
      <p class="appointment__line">DATE ....\....\....</p>
      <p class="appointment__line">TIME &nbsp;....:.....</p>
    </div>

    <ul class="contact">
      <li class="contact__address">218 Alder Avenue Fairview, CO 80422</li>
      <li class="contact__phone">970-555-0142</li>
      <li class="contact__web">glowhavenbymarisol.com</li>
    </ul>
  </section>
</main>
</body>
</html>
```